Business Card Design for a Personal Trainer

I need a business card design for my job as a personal trainer. It should have a unique, modern and exclusive design. On the front there should be only my logo with my name and my job. 0162/3819204 Tobias Lendhart Wiesengrundweg 14 80417 Munich Germany The most important contact information is the web adress. it can be bigger than the rest, but its not necessary. The card should be 8,5cmx5,5cm big. Font: Roboto. Colors: black, white, gray, 56c1ff.

```html
<!DOCTYPE html>
<html lang="de">
<head>
<meta charset="utf-8">
<title>Tobias Lendhart – Personal Trainer Visitenkarte</title>
<link rel="stylesheet" href="https://fonts.googleapis.com/css2?family=Open+Sans:wght@400;600&display=swap">
<style>
  :root {
    --stage: #e4e4e4;
    --card-black: #141414;
    --card-black-soft: #242424;
    --white: #ffffff;
    --gray: #9a9a9a;
    --accent: #56c1ff;
    --frame: #ffffff;
  }
  * { margin: 0; padding: 0; box-sizing: border-box; }
  html, body { width: 1200px; height: 864px; overflow: hidden; }
  body {
    background: radial-gradient(ellipse at 50% 40%, #f2f2f2 0%, var(--stage) 70%, #cfcfcf 100%);
    font-family: "Open Sans", sans-serif;
    color: var(--white);
    position: relative;
  }
  .card {
    position: absolute;
    top: 264px;
    width: 520px;
    height: 336px;
    background: radial-gradient(ellipse at 40% 30%, var(--card-black-soft) 0%, var(--card-black) 75%);
    box-shadow: 0 10px 28px rgba(0,0,0,0.25);
    overflow: hidden;
  }
  .card--contact { left: 50px; }
  .card--front { left: 630px; }

  /* wordmark */
  .wordmark { position: absolute; text-align: center; }
  .wordmark__name {
    display: flex; align-items: center; gap: 8px;
    font-weight: 400; letter-spacing: 1px; text-transform: uppercase;
    color: var(--white);
  }
  .wordmark__dot { width: 9px; height: 9px; background: var(--white); }
  .wordmark__job {
    margin-top: 3px; padding-top: 2px;
    border-top: 1px solid var(--gray);
    font-size: 8px; letter-spacing: 3px; text-transform: uppercase; color: var(--gray);
  }

  /* contact side */
  .card--contact .wordmark { left: 26px; top: 34px; }
  .card--contact .wordmark__name { font-size: 17px; }
  .contact {
    position: absolute; right: 30px; top: 40px; width: 190px;
  }
  .contact__name { font-size: 17px; font-weight: 600; margin-bottom: 8px; }
  .contact__line {
    display: flex; align-items: center; gap: 8px;
    font-size: 12px; line-height: 1.6; color: var(--white);
  }
  .contact__line svg { width: 11px; height: 11px; flex: none; }

  .gallery {
    position: absolute; left: 0; right: 0; top: 128px; height: 118px;
    display: flex; gap: 8px; padding: 8px;
    background: var(--frame);
  }
  .gallery__photo { flex: 1; }
  .gallery__photo--forest { background: linear-gradient(160deg, #6b5a3c, #2f2a1e); }
  .gallery__photo--mat { background: linear-gradient(160deg, #d8d2c8, #4fa9b5); }
  .gallery__photo--gym { background: linear-gradient(160deg, #b8bcc0, #3a3c3f); }
  .gallery__photo--stretch { background: linear-gradient(160deg, #c9a25a, #5b4a2c); }

  .address {
    position: absolute; left: 28px; bottom: 44px;
    font-size: 15px; letter-spacing: 0.3px;
  }

  /* front side */
  .portrait {
    position: absolute; left: 24px; bottom: 0; width: 190px; height: 290px;
    background: linear-gradient(180deg, #5a5a5a 0%, #2e2e2e 60%, #1c1c1c 100%);
    border-radius: 90px 90px 0 0;
  }
  .card--front .wordmark { left: 240px; top: 110px; }
  .card--front .wordmark__name { font-size: 20px; }
  .card--front .wordmark__job { font-size: 9px; }
  .website {
    position: absolute; right: 24px; bottom: 56px;
    font-size: 21px; color: var(--accent); letter-spacing: 0.2px;
  }
</style>
</head>
<body>

<section class="card card--contact">
  <div class="wordmark">
    <div class="wordmark__name"><span class="wordmark__dot"></span>Tobias Lendhart</div>
    <div class="wordmark__job">Personal Trainer</div>
  </div>

  <div class="contact">
    <p class="contact__name">Tobias Lendhart</p>
    <p class="contact__line">
      <svg viewBox="0 0 24 24" aria-hidden="true"><path fill="#ffffff" d="M6.6 10.8a15.1 15.1 0 0 0 6.6 6.6l2.2-2.2a1 1 0 0 1 1-.25 11.4 11.4 0 0 0 3.6.57 1 1 0 0 1 1 1V20a1 1 0 0 1-1 1A17 17 0 0 1 3 4a1 1 0 0 1 1-1h3.5a1 1 0 0 1 1 1c0 1.25.2 2.45.57 3.57a1 1 0 0 1-.25 1z"/></svg>
      0162/3819204
    </p>
    <p class="contact__line">
      <svg viewBox="0 0 24 24" aria-hidden="true"><rect x="2" y="5" width="20" height="14" fill="none" stroke="#ffffff" stroke-width="2"/><path d="M2 5l10 8 10-8" fill="none" stroke="#ffffff" stroke-width="2"/></svg>
      t.lendhart@kraftpost.de
    </p>
  </div>

  <div class="gallery">
    <div class="gallery__photo gallery__photo--forest" role="img" aria-label="Waldweg zwischen hohen Bäumen"></div>
    <div class="gallery__photo gallery__photo--mat" role="img" aria-label="Hände rollen eine türkise Yogamatte aus"></div>
    <div class="gallery__photo gallery__photo--gym" role="img" aria-label="Fitnessstudio mit Hantelreihen"></div>
    <div class="gallery__photo gallery__photo--stretch" role="img" aria-label="Frau beim Dehnen im Wald"></div>
  </div>

  <p class="address">Wiesengrundweg 14 , 80417 München</p>
</section>

<section class="card card--front">
  <div class="portrait" role="img" aria-label="Schwarzweißporträt des Trainers mit verschränkten Armen"></div>
  <div class="wordmark">
    <div class="wordmark__name"><span class="wordmark__dot"></span>Tobias Lendhart</div>
    <div class="wordmark__job">Personal Trainer</div>
  </div>
  <p class="website">www.tobiaslendhart.de</p>
</section>

</body>
</html>
```